Website redesign www.marigoldlawpc.com law firm site

Need to redesign the website that I currently have to look more modern and professional. Would also like to be able to make updates and post without having a huge hassle. See current www.marigoldlawpc.com. I just think that it looks very immature and it's very templated there's no ability for me to make posts or Add links or anything like that

Target Market(s)

California people looking for a powerhouse attorney in

Industry/Entity Type

Legal

Number of Pages Required

3 page

Font styles to use
Serif
Sans Serif

Colors
ec1f27
000000
ffffff

Requirements
Must have
• Must be mobile friendly. Must look professional and have ability to post links to other websites. Must have ability to post blogs or articles. Would like to be able to read my FeeTrove account and also have the ability to upload forms for people to download
Nice to have
• Simple design easy to use and not cluttered with too much text

```html
<!DOCTYPE html>
<html lang="en">
<head>
<meta charset="utf-8">
<title>Marigold Law P.C.</title>
<link rel="stylesheet" href="https://fonts.googleapis.com/css2?family=Cinzel:wght@400;700&family=Open+Sans:wght@400;600;700&display=swap">
<style>
:root{
  --red:#ec1f27;
  --red-deep:#c8141b;
  --black:#000000;
  --ink:#1d1d1d;
  --text:#555555;
  --muted:#8a8a8a;
  --white:#ffffff;
  --grey-band:#ececec;
  --line:#cfcfcf;
}
*{box-sizing:border-box;margin:0;padding:0}
html,body{width:1200px;height:2483px;overflow:hidden;background:var(--white)}
body{position:relative;font-family:"Open Sans",Arial,sans-serif;color:var(--text)}
.abs{position:absolute}

/* header */
.site-header{position:absolute;left:0;top:0;width:1200px;height:80px;background:var(--white)}
.brand{position:absolute;left:162px;top:26px;display:flex;align-items:center;gap:10px;white-space:nowrap}
.brand-mark{width:16px;height:16px;background:var(--red)}
.brand-name{font-family:"Open Sans",Arial,sans-serif;font-size:22px;line-height:28px;font-weight:700;color:var(--ink)}
.contact-top{position:absolute;left:722px;top:24px;font-size:13px;line-height:17px;color:var(--ink)}
.contact-top .mail{color:var(--muted)}
.phone-icon{position:absolute;left:692px;top:24px}
.social-top{position:absolute;top:25px;display:flex;gap:10px;left:937px}
.social-top span{width:26px;height:26px;border-radius:4px;background:#3b5b9a}
.social-top span:nth-child(2){background:#1b73b0}
.social-top span:nth-child(3){background:#19a6d8}

/* nav */
.main-nav{position:absolute;left:0;top:80px;width:1200px;height:35px;background:linear-gradient(#2b2b2b,#050505)}
.main-nav ul{list-style:none;position:relative;height:35px}
.main-nav li{position:absolute;top:0;height:35px;line-height:35px;font-family:"Cinzel",Georgia,serif;font-size:12px;font-weight:700;color:var(--white);text-align:center;white-space:nowrap}
.main-nav li.active{background:var(--red);border-top:3px solid #ff5a60;line-height:31px}
.main-nav .sep{position:absolute;top:12px;width:1px;height:12px;background:#666}

/* hero */
.hero{position:absolute;left:0;top:115px;width:1200px;height:455px;background:linear-gradient(160deg,#e4e4e4 0%,#b9b9b9 35%,#6b6b6b 70%,#3a3a3a 100%)}
.hero-arrow{position:absolute;top:182px;width:30px;height:84px;background:rgba(120,120,120,.55)}
.hero-caption{position:absolute;left:165px;top:165px;width:332px;height:75px;background:rgba(25,25,25,.82);padding:8px 0 0 8px;color:var(--white);font-family:"Cinzel",Georgia,serif;white-space:nowrap}
.hero-caption .small{font-size:18px;line-height:20px}
.hero-caption .big{font-size:36px;line-height:42px}
.btn-red{position:absolute;background:var(--red);color:var(--white);font-family:"Cinzel",Georgia,serif;font-size:13px;font-weight:700;display:flex;align-items:center;justify-content:center;gap:8px;white-space:nowrap}
.thumbs{position:absolute;left:523px;top:430px;display:flex;gap:6px;padding:3px;background:var(--white)}
.thumbs span{width:48px;height:34px;background:linear-gradient(#c9d3dc,#8593a0)}
.thumbs span:nth-child(2){background:linear-gradient(#f1e4e4,#c9a2a2)}

/* section titles */
.section-title{position:absolute;left:0;width:1200px;text-align:center;font-family:"Cinzel",Georgia,serif;font-size:29px;font-weight:400;color:var(--ink)}
.section-title em{font-style:normal;color:var(--red)}
.title-rule{position:absolute;left:560px;width:80px;height:1px;background:#888}

/* welcome */
.welcome-text{position:absolute;left:165px;top:686px;width:870px;text-align:center;font-size:12.5px;line-height:26.5px;color:#666}
.btn-outline{position:absolute;border:2px solid var(--ink);color:var(--ink);font-family:"Cinzel",Georgia,serif;font-size:13px;font-weight:700;display:flex;align-items:center;justify-content:center;gap:8px;background:var(--white);white-space:nowrap}

/* practice */
.practice{position:absolute;left:0;top:892px;width:1200px;height:405px;background:linear-gradient(115deg,#f3f3f3 0%,#e9e6e4 40%,#efefef 60%,#e2e2e2 100%)}
.practice-veil{position:absolute;inset:0;background:rgba(255,255,255,.55)}
.practice-banner{position:absolute;left:568px;top:101px;width:64px;height:258px;background:var(--white);display:flex;align-items:center;justify-content:center}
.practice-banner span{transform:rotate(-90deg);white-space:nowrap;font-family:"Cinzel",Georgia,serif;font-size:30px;color:var(--ink)}
.practice-banner em{font-style:normal;color:var(--red)}
.area{position:absolute;width:215px}
.area h3{font-family:"Cinzel",Georgia,serif;font-size:15px;font-weight:700;color:var(--ink);margin-bottom:2px}
.area p{font-size:11.5px;line-height:16px;color:#666}
.area.left{text-align:right}
.area-icon{position:absolute}
.connector{position:absolute;height:1px;background:#c4c4c4}
.connector::before,.connector::after{content:"";position:absolute;top:-2px;width:5px;height:5px;border-radius:50%;background:#aaa}
.connector::before{left:0}.connector::after{right:0}

/* testimonials */
.quote{position:absolute;width:275px}
.avatar{position:absolute;left:0;top:3px;width:58px;height:58px;border-radius:50%;border:2px solid #ddd;background:radial-gradient(circle at 50% 40%,#c7a58c,#6b5445)}
.quote p{position:absolute;left:67px;top:0;width:208px;font-size:11.5px;line-height:18.5px;color:#666;text-indent:34px}
.quote .qm{position:absolute;font-family:Georgia,serif;font-size:34px;color:#c9c9c9;line-height:1}
.quote h4{position:absolute;left:67px;top:102px;font-family:"Cinzel",Georgia,serif;font-size:13px;font-weight:700;color:var(--ink)}

/* ratings */
.ratings{position:absolute;left:0;top:1688px;width:1200px;height:165px;background:var(--grey-band)}
.ratings-tag{position:absolute;left:162px;top:-5px;width:258px;height:40px;background:var(--red);color:var(--white);font-family:"Cinzel",Georgia,serif;font-size:21px;line-height:40px;padding-left:18px;transform:skewY(-1.5deg);white-space:nowrap}
.ratings p{position:absolute;left:165px;top:62px;width:330px;font-size:11.5px;line-height:20px;color:#666}
.badge-divider{position:absolute;top:72px;width:1px;height:50px;background:#c8c8c8}

/* contact */
.contact{position:absolute;left:0;top:1853px;width:1200px;height:630px;background:linear-gradient(180deg,#4d5866 0%,#2a323d 45%,#161b22 100%)}
.contact .section-title{color:var(--white)}
.contact-panel{position:absolute;left:257px;top:147px;width:685px;height:380px;background:rgba(200,20,27,.82)}
.send-badge{position:absolute;left:573px;top:125px;width:54px;height:54px;border-radius:50%;background:var(--white);display:flex;align-items:center;justify-content:center}
.contact-lines{position:absolute;left:257px;top:193px;width:685px;text-align:center;color:var(--white);font-size:11.5px;line-height:20px;font-weight:600}
.field{position:absolute;background:rgba(255,255,255,.22);color:var(--white);font-size:11px;font-weight:600;padding:8px 12px}
.btn-ghost{position:absolute;left:530px;top:464px;width:140px;height:35px;border:1px solid var(--white);color:var(--white);font-family:"Cinzel",Georgia,serif;font-size:13px;font-weight:700;display:flex;align-items:center;justify-content:center;gap:8px;white-space:nowrap}
.footer-nav{position:absolute;left:0;top:546px;width:1200px;display:flex;justify-content:center;color:var(--white);font-family:"Cinzel",Georgia,serif;font-size:11px;font-weight:700;white-space:nowrap}
.footer-nav span{padding:0 22px;border-right:1px solid #aaa}
.footer-nav span:last-child{border-right:0}
.footer-rule{position:absolute;left:0;top:577px;width:1200px;height:1px;background:rgba(255,255,255,.25)}
.copyright{position:absolute;left:165px;top:597px;color:var(--white);font-size:11.5px;font-weight:600}
.social-foot{position:absolute;left:935px;top:590px;display:flex;gap:12px}
.social-foot span{width:28px;height:28px;border-radius:50%;border:1.5px solid var(--red)}
</style>
</head>
<body>

<header class="site-header">
  <div class="brand"><span class="brand-mark"></span><span class="brand-name">Marigold Law P.C.</span></div>
  <svg class="phone-icon" width="14" height="30" viewBox="0 0 14 30"><rect x="1" y="1" width="12" height="28" rx="2" fill="#9a9a9a"/><rect x="3" y="5" width="8" height="18" fill="#e6e6e6"/></svg>
  <div class="contact-top">(555) 014-2290<br><span class="mail">dana@marigoldlawgroup.com</span></div>
  <div class="social-top"><span></span><span></span><span></span></div>
</header>

<nav class="main-nav">
  <ul>
    <li class="active" style="left:162px;width:113px">Home</li>
    <li style="left:295px;width:150px">Attorney Profile</li>
    <li class="sep" style="left:460px"></li>
    <li style="left:478px;width:150px">Practice Areas</li>
    <li class="sep" style="left:640px"></li>
    <li style="left:650px;width:150px">Client Reviews</li>
    <li class="sep" style="left:812px"></li>
    <li style="left:820px;width:90px">Links</li>
    <li class="sep" style="left:922px"></li>
    <li style="left:920px;width:150px">Contact Us</li>
  </ul>
</nav>

<section class="hero" role="img" aria-label="Photo of hands signing a document at a glass desk">
  <div class="hero-arrow" style="left:0"><svg width="30" height="84"><path d="M19 36 L11 42 L19 48 Z" fill="none" stroke="#222" stroke-width="1.5"/></svg></div>
  <div class="hero-arrow" style="left:1170px"><svg width="30" height="84"><path d="M11 36 L19 42 L11 48 Z" fill="none" stroke="#222" stroke-width="1.5"/></svg></div>
  <div class="hero-caption"><div class="small">The Greatest Firm</div><div class="big">You Can Trust</div></div>
  <div class="btn-red" style="left:162px;top:250px;width:120px;height:32px">More Info <svg width="7" height="9"><path d="M0 0L7 4.5L0 9Z" fill="#fff"/></svg></div>
  <div class="thumbs" role="img" aria-label="Slide thumbnails"><span></span><span></span><span></span></div>
</section>

<h2 class="section-title" style="top:628px">Welcome To &nbsp;<em>Marigold Law P.C.</em></h2>
<div class="title-rule" style="top:673px"></div>
<p class="welcome-text">Marigold Law P.C. is owned by Dana L. Marigold, a dedicated and caring professional who uses her broad range of skills as a California lawyer to bring consumers and business owners exceptionally strong legal representation that achieves best results. She works with people from across the northern region of California, from the Northern border to the Central Valley region. They bring her legal concerns and problems that occur in many areas of law, including Real Estate, Family law, Business Law, Bankruptcy, Criminal Law and Civil Litigation.</p>
<div class="btn-red" style="left:460px;top:811px;width:120px;height:34px">Read More <svg width="7" height="9"><path d="M0 0L7 4.5L0 9Z" fill="#fff"/></svg></div>
<div class="btn-outline" style="left:585px;top:811px;width:155px;height:34px">Download Form <svg width="7" height="9"><path d="M0 0L7 4.5L0 9Z" fill="#1d1d1d"/></svg></div>

<section class="practice" role="img" aria-label="Faded photo of a house model on paperwork">
  <div class="practice-veil"></div>
  <h2 class="section-title" style="top:25px">Practice <em>Areas</em></h2>
  <div class="title-rule" style="top:67px"></div>
  <div class="practice-banner"><span>Marigold <em>Law</em></span></div>

  <div class="area left" style="left:192px;top:118px"><h3>Business Law</h3><p>Lorem ipsum dolor sit onsectetue wisi enim ad minim veniam,...</p></div>
  <div class="area left" style="left:192px;top:202px"><h3>Real Estate Law</h3><p>Lorem ipsum dolor sit onsectetue wisi enim ad minim veniam, ...</p></div>
  <div class="area left" style="left:192px;top:285px"><h3>Bankruptcy</h3><p>Lorem ipsum dolor sit onsectetue wisi enim ad minim veniam,...</p></div>
  <div class="area" style="left:805px;top:118px"><h3>Family Law</h3><p>Lorem ipsum dolor sit onsectetue wisi enim ad minim veniam,...</p></div>
  <div class="area" style="left:805px;top:202px"><h3>Criminal Law</h3><p>Lorem ipsum dolor sit onsectetue wisi enim ad minim veniam, ...</p></div>
  <div class="area" style="left:805px;top:285px"><h3>Civil Litigation</h3><p>Lorem ipsum dolor sit onsectetue wisi enim ad minim veniam,...</p></div>

  <div class="connector" style="left:475px;top:141px;width:80px"></div>
  <div class="connector" style="left:475px;top:225px;width:80px"></div>
  <div class="connector" style="left:475px;top:308px;width:80px"></div>
  <div class="connector" style="left:645px;top:141px;width:80px"></div>
  <div class="connector" style="left:645px;top:225px;width:80px"></div>
  <div class="connector" style="left:645px;top:308px;width:80px"></div>

  <svg class="area-icon" style="left:422px;top:124px" width="46" height="36" viewBox="0 0 46 36" fill="none" stroke="#ec1f27" stroke-width="2"><rect x="2" y="8" width="42" height="26" rx="2"/><path d="M16 8V3h14v5M2 18h42"/></svg>
  <svg class="area-icon" style="left:425px;top:205px" width="40" height="38" viewBox="0 0 40 38" fill="none" stroke="#ec1f27" stroke-width="2"><path d="M3 18L20 3l17 15M8 14v22h24V14"/><rect x="15" y="20" width="10" height="9"/></svg>
  <svg class="area-icon" style="left:428px;top:285px" width="36" height="42" viewBox="0 0 36 42" fill="none" stroke="#ec1f27" stroke-width="2"><path d="M12 4h12l-4 8h-4zM16 12C6 16 3 28 6 36h24c3-8 0-20-10-24"/></svg>
  <svg class="area-icon" style="left:744px;top:121px" width="40" height="40" viewBox="0 0 40 40" fill="none" stroke="#ec1f27" stroke-width="2"><circle cx="12" cy="7" r="4"/><circle cx="28" cy="7" r="4"/><path d="M7 38V14h10v24M23 38V14h10v24"/></svg>
  <svg class="area-icon" style="left:737px;top:208px" width="54" height="34" viewBox="0 0 54 34" fill="none" stroke="#ec1f27" stroke-width="2"><circle cx="14" cy="20" r="11"/><circle cx="40" cy="14" r="11"/><path d="M24 16l6-2"/></svg>
  <svg class="area-icon" style="left:740px;top:288px" width="44" height="40" viewBox="0 0 44 40" fill="none" stroke="#ec1f27" stroke-width="2"><path d="M8 12l12-10 6 7-12 10zM20 14l16 16M4 38h22"/></svg>
</section>

<h2 class="section-title" style="top:1345px">What People Say <em>About Us?</em></h2>
<div class="title-rule" style="top:1389px"></div>

<div class="quote" style="left:165px;top:1430px">
  <div class="avatar" role="img" aria-label="Client portrait"></div>
  <span class="qm" style="left:80px;top:-6px">&ldquo;</span>
  <p>Mattis porttitor nulla, eget eleif end metus gravida id . Nune sollicit udin nune at tellus pretium a pulvinar purus. Mattis porttitor null, eget eleifend mentus.</p>
  <span class="qm" style="left:228px;top:78px">&rdquo;</span>
  <h4>Lorem Ispum</h4>
</div>
<div class="quote" style="left:463px;top:1430px">
  <div class="avatar" role="img" aria-label="Client portrait"></div>
  <span class="qm" style="left:80px;top:-6px">&ldquo;</span>
  <p>Mattis porttitor nulla, eget eleif end metus gravida id . Nune sollicit udin nune at tellus pretium a pulvinar purus. Mattis porttitor null, eget eleifend mentus.</p>
  <span class="qm" style="left:228px;top:78px">&rdquo;</span>
  <h4>Lorem Ispum</h4>
</div>
<div class="quote" style="left:761px;top:1430px">
  <div class="avatar" role="img" aria-label="Client portrait"></div>
  <span class="qm" style="left:80px;top:-6px">&ldquo;</span>
  <p>Mattis porttitor nulla, eget eleif end metus gravida id . Nune sollicit udin nune at tellus pretium a pulvinar purus. Mattis porttitor null, eget eleifend mentus.</p>
  <span class="qm" style="left:228px;top:78px">&rdquo;</span>
  <h4>Lorem Ispum</h4>
</div>

<div class="btn-outline" style="left:540px;top:1596px;width:125px;height:34px">View More <svg width="7" height="9"><path d="M0 0L7 4.5L0 9Z" fill="#1d1d1d"/></svg></div>

<section class="ratings">
  <div class="ratings-tag">Ratings &amp; Reviews</div>
  <p>Alore eu feugiat nulla facilisis at vero eros e accumsan et iusto odio dignissim qui blandit praesent luptatum zzril delenit augueugait nulla facilisi.</p>
  <div class="abs" role="img" aria-label="Rating badge" style="left:522px;top:55px;width:82px;height:82px;border-radius:50%;background:#d9d9d9;border:3px solid #1f4f8f"></div>
  <div class="badge-divider" style="left:645px"></div>
  <div class="abs" role="img" aria-label="Bar association seal" style="left:683px;top:58px;width:76px;height:76px;border-radius:50%;background:#f4f4f4;border:2px solid #555"></div>
  <div class="badge-divider" style="left:798px"></div>
  <div class="abs" role="img" aria-label="Lawyer directory badge" style="left:840px;top:80px;width:196px;height:34px;background:#c9d0da"></div>
</section>

<section class="contact" role="img" aria-label="Dark photo of business people shaking hands in an office">
  <h2 class="section-title" style="top:37px">Contact <em>Us</em></h2>
  <div class="title-rule" style="top:79px;background:#bbb"></div>
  <div class="contact-panel"></div>
  <div class="send-badge"><svg width="26" height="24" viewBox="0 0 26 24" fill="none" stroke="#1d1d1d" stroke-width="1.6"><path d="M2 11L24 2 17 22 12 14zM12 14L24 2"/></svg></div>
  <div class="contact-lines">Marigold Law, P.C. Office 418 Orchard Lane &nbsp;Suite 200 Fairview, CA 95000<br>dana@marigoldlawgroup.com<br>(555) 014-2290</div>
  <div class="field" style="left:297px;top:277px;width:299px;height:35px">Name</div>
  <div class="field" style="left:603px;top:277px;width:300px;height:35px">Email</div>
  <div class="field" style="left:297px;top:318px;width:606px;height:130px">Message</div>
  <div class="btn-ghost">Send Message <svg width="7" height="9"><path d="M0 0L7 4.5L0 9Z" fill="#fff"/></svg></div>
  <div class="footer-nav"><span>Home</span><span>Attorney Profile</span><span>Practice Areas</span><span>Client Reviews</span><span>Links</span><span>Contact Us</span></div>
  <div class="footer-rule"></div>
  <div class="copyright">Copyright &copy; 2016 - Marigoldlawpc | All Rights Reserved</div>
  <div class="social-foot"><span></span><span></span><span></span></div>
</section>

</body>
</html>
```